Velk Partners Building Business Cards

We need a business card that reflects our business as "Solar Experts" in San Diego. Browse our website www.velkpartners.example our License needs to be displayed as "CSLB# 3867140" our phone number is (619) 555-0187

Save thousands on your electric bills and increase the value of your home while helping to protect the environment. Our solar installation experts will help you design the system that's right for you, using only the highest quality equipment that will look great and give you ideal performance. Our goal is to make you energy independent, and get your electric bill to 0.

Paul Osterby
(619) 555-0187
paul@velkpartners.example

Target Market(s)

Home owners in san diego looking for solar

Industry/Entity Type

Solar Energy

Contact Information for Business Card

Paul Osterby
(619) 555-0187
paul@velkpartners.example

Font styles to use
Other font styles liked:
• Use our logo font

Requirements
Must have
• License needs to be displayed as "CSLB# 3867140" our phone number is (619) 555-0187
Nice to have
• Real images of rooftop home solar in san diego
Should not have
• our business address

```html
<!DOCTYPE html>
<html lang="en">
<head>
<meta charset="utf-8">
<title>Velk Partners Building – Business Card</title>
<link rel="stylesheet" href="https://fonts.googleapis.com/css2?family=Cinzel:wght@400;600&family=Montserrat:wght@700;800&display=swap">
<style>
  :root {
    --page-bg: #e9ebee;
    --brand-blue: #124a8c;
    --brand-yellow: #f6b21c;
    --ink-dark: #123766;
    --white: #ffffff;
    --photo-sky: #6f95c4;
    --photo-panel: #1f3767;
    --photo-roof: #8a8577;
  }
  * { margin: 0; padding: 0; box-sizing: border-box; }
  html, body { width: 1200px; height: 900px; overflow: hidden; }
  body {
    background: var(--page-bg);
    display: flex;
    flex-direction: column;
    align-items: center;
    justify-content: center;
    gap: 40px;
  }
  .card {
    position: relative;
    width: 630px;
    height: 360px;
    overflow: hidden;
    box-shadow: 0 8px 24px rgba(0,0,0,.18);
  }
  .card-bands { position: absolute; inset: 0; }

  /* Front */
  .front-photo {
    position: absolute; inset: 0;
    background: linear-gradient(160deg, var(--photo-sky) 0%, var(--photo-panel) 38%, #2b4d86 60%, var(--photo-roof) 100%);
  }
  .front-brand {
    position: absolute;
    left: 60px; top: 150px;
    display: flex; align-items: center; gap: 14px;
  }
  .brand-dot {
    width: 26px; height: 26px; border-radius: 50%;
    background: var(--brand-yellow);
  }
  .brand-name {
    font-family: "Montserrat", sans-serif;
    font-weight: 800;
    font-size: 38px;
    letter-spacing: -0.5px;
    color: var(--white);
  }
  .front-url {
    position: absolute;
    left: 230px; top: 238px;
    font-family: "Cinzel", serif;
    font-size: 13px;
    letter-spacing: 1px;
    color: var(--white);
  }

  /* Back */
  .back { background: var(--brand-blue); }
  .back-brand {
    position: absolute; left: 50px; top: 112px;
    display: flex; align-items: center; gap: 14px;
  }
  .back-brand .brand-dot { width: 52px; height: 52px; }
  .back-brand .brand-name { font-size: 26px; }
  .holder-name {
    position: absolute; right: 40px; top: 118px;
    font-family: "Montserrat", sans-serif;
    font-weight: 700;
    font-size: 24px;
    color: var(--white);
  }
  .contact-list {
    position: absolute; left: 40px; top: 222px;
    list-style: none;
    font-family: "Cinzel", serif;
    font-size: 14px;
    color: var(--white);
    letter-spacing: .5px;
  }
  .contact-list li { display: flex; align-items: center; gap: 10px; line-height: 21px; }
  .contact-icon { width: 12px; height: 12px; flex: none; }
  .license {
    position: absolute; left: 452px; top: 300px; width: 130px;
    text-align: center;
    font-family: "Cinzel", serif;
    font-weight: 600;
    font-size: 14px;
    color: var(--ink-dark);
  }
</style>
</head>
<body>

  <section class="card front" aria-label="Card front">
    <div class="front-photo" role="img" aria-label="Photo of rooftop solar panels on a San Diego home"></div>
    <svg class="card-bands" viewBox="0 0 630 360" aria-hidden="true">
      <rect x="0" y="286" width="630" height="4" fill="var(--brand-yellow)"/>
      <polygon points="300,290 470,290 455,306 315,306" fill="var(--brand-yellow)"/>
      <rect x="0" y="290" width="630" height="70" fill="var(--brand-blue)" opacity=".55"/>
      <rect x="0" y="340" width="630" height="8" fill="var(--brand-yellow)"/>
    </svg>
    <div class="front-brand">
      <span class="brand-dot"></span>
      <span class="brand-name">Velk Partners Building</span>
    </div>
    <p class="front-url">www.velkpartners.example</p>
  </section>

  <section class="card back" aria-label="Card back">
    <svg class="card-bands" viewBox="0 0 630 360" aria-hidden="true">
      <line x1="40" y1="212" x2="380" y2="156" stroke="var(--brand-yellow)" stroke-width="1"/>
      <line x1="380" y1="156" x2="600" y2="156" stroke="var(--brand-yellow)" stroke-width="1"/>
      <rect x="0" y="318" width="630" height="4" fill="var(--brand-yellow)"/>
      <polygon points="440,318 452,296 596,296 608,318" fill="var(--brand-yellow)"/>
      <rect x="0" y="336" width="630" height="24" fill="var(--brand-yellow)"/>
    </svg>
    <div class="back-brand">
      <span class="brand-dot"></span>
      <span class="brand-name">Velk Partners Building</span>
    </div>
    <p class="holder-name">Paul Osterby</p>
    <ul class="contact-list">
      <li>
        <svg class="contact-icon" viewBox="0 0 12 12" aria-hidden="true"><path d="M2.5 1 L4.5 1 L5.2 3.5 L4 4.5 Q5 7 7.5 8 L8.5 6.8 L11 7.5 L11 9.5 Q10.5 11 9 11 Q1 10 1 2.5 Q1 1 2.5 1Z" fill="var(--brand-yellow)"/></svg>
        (619) 555-0187
      </li>
      <li>
        <svg class="contact-icon" viewBox="0 0 12 12" aria-hidden="true"><rect x="0.5" y="2" width="11" height="8" fill="none" stroke="var(--brand-yellow)" stroke-width="1.3"/><path d="M0.5 2 L6 6.5 L11.5 2" fill="none" stroke="var(--brand-yellow)" stroke-width="1.3"/></svg>
        paul@velkpartners.example
      </li>
      <li>
        <svg class="contact-icon" viewBox="0 0 12 12" aria-hidden="true"><circle cx="6" cy="6" r="5" fill="none" stroke="var(--brand-yellow)" stroke-width="1.3"/><path d="M1 6 H11 M6 1 Q3 6 6 11 Q9 6 6 1" fill="none" stroke="var(--brand-yellow)" stroke-width="1"/></svg>
        www.velkpartners.example
      </li>
    </ul>
    <p class="license">CSLB# 3867140</p>
  </section>

</body>
</html>
```